New letter head for Air Conditioning business

We need a new professional letter head design to suit our new re-branded air conditioning business. Our new logo is attached

```html
<!DOCTYPE html>
<html lang="en">
<head>
<meta charset="UTF-8">
<title>Norval Letterhead</title>
<link rel="stylesheet" href="https://fonts.googleapis.com/css2?family=Poppins:wght@400;500;600;700&display=swap">
<style>
  :root {
    --backdrop: #ececec;
    --paper: #e1f2e6;
    --brand-green: #67c28a;
    --white: #ffffff;
    --ink: #111111;
    --logo-ink: #3a3a3a;
  }
  * { margin: 0; padding: 0; box-sizing: border-box; }
  html, body {
    width: 1200px; height: 1200px; overflow: hidden;
    background: var(--backdrop);
    font-family: "Poppins", sans-serif;
    color: var(--ink);
  }
  .letterhead {
    position: absolute; left: 194px; top: 18px;
    width: 811px; height: 1164px;
    background: var(--paper);
    overflow: hidden;
  }
  .corner-art { position: absolute; }
  .corner-art-top {
    left: 0; top: 0; width: 300px; height: 185px;
    background: linear-gradient(160deg, var(--white) 0%, var(--brand-green) 100%);
  }
  .corner-art-bottom {
    right: 0; bottom: 0; width: 300px; height: 180px;
    background: linear-gradient(340deg, var(--white) 0%, var(--brand-green) 100%);
  }
  .brand { position: absolute; left: 470px; top: 58px; display: flex; align-items: center; gap: 16px; }
  .brand-dot { width: 34px; height: 34px; border-radius: 50%; background: var(--brand-green); }
  .brand-name { font-size: 42px; font-weight: 600; letter-spacing: 4px; color: var(--logo-ink); line-height: 1; }
  .brand-tagline {
    position: absolute; left: 520px; top: 108px;
    font-size: 8.4px; font-weight: 600; letter-spacing: 2.1px; color: var(--brand-green);
  }
  .recipient-name { position: absolute; left: 64px; top: 254px; font-size: 20px; font-weight: 700; }
  .letter-date { position: absolute; right: 81px; top: 254px; font-size: 20px; font-weight: 700; }
  .recipient-address { position: absolute; left: 64px; top: 292px; font-size: 19px; font-weight: 500; }
  .letter-body {
    position: absolute; left: 64px; width: 686px;
    font-size: 14.9px; line-height: 18.6px; text-align: justify;
    letter-spacing: 0.1px;
  }
  .para-one { top: 359px; }
  .para-two { top: 576px; }
  .closing { position: absolute; left: 64px; top: 694px; font-size: 20px; font-weight: 500; }
  .signature-area {
    position: absolute; left: 64px; top: 758px; width: 168px; height: 56px;
    background: linear-gradient(90deg, rgba(17,17,17,0.10), rgba(17,17,17,0.04));
    border-radius: 4px;
  }
  .sender-name { position: absolute; left: 64px; top: 854px; font-size: 20px; font-weight: 500; }
  .sender-role { position: absolute; left: 64px; top: 889px; font-size: 20px; font-weight: 500; }
  .contact-icon { position: absolute; left: 64px; }
  .contact-text { position: absolute; left: 117px; }
  .phone-icon { top: 1014px; }
  .phone-text { top: 1010px; font-size: 16px; line-height: 20px; }
  .web-icon { top: 1063px; }
  .web-text { top: 1070px; font-size: 12.5px; }
  .mail-icon { top: 1112px; }
  .mail-text { top: 1112px; font-size: 12.5px; }
</style>
</head>
<body>
  <div class="letterhead">
    <div class="corner-art corner-art-top" role="img" aria-label="Decorative green corner artwork"></div>
    <div class="corner-art corner-art-bottom" role="img" aria-label="Decorative green corner artwork"></div>

    <div class="brand">
      <span class="brand-dot"></span>
      <span class="brand-name">NORVAL</span>
    </div>
    <div class="brand-tagline">AIR CONDITIONING &amp; REFRIGERATION</div>

    <div class="recipient-name">Your&nbsp; Name Here</div>
    <div class="letter-date">Date : 2.6.2021</div>
    <div class="recipient-address">Address</div>

    <p class="letter-body para-one">Lorem ipsum dolor sit amet, consectetur adipiscing elit. Nam pretium quam eget feugiat tincidunt. Nullam consequat mi vitae pharetra sagittis. Suspendisse porta placerat velit, ac condimentum felis molestie in. Nullam eget velit in erat consectetur semper vitae ac nisi. Donec et lectus ut purus aliquam pulvinar non in arcu. Vestibulum et turpis a nisl placerat euismod. Aliquam eu quam augue. Cras consectetur, velit ut semper aliquam, odio tortor suscipit nulla, et vulputate dui risus at ante. Maecenas ac dignissim ex. Pellentesque in dignissim massa. Fusce at posuere lorem. Vivamus molestie nisl ac nisi rhoncus vulputate. Aenean augue arcu, maximus ut consequat in, lobortis sit amet lectus. Suspendisse dapibus auctor quam, sed tempor orci euismod accumsan. In hac habitasse platea dictumst. Suspendisse ut enim metus.</p>

    <p class="letter-body para-two">Nullam at mi eros. Lorem ipsum dolor sit amet, consectetur adipiscing elit. Vestibulum tempus, sem id pharetra ultrices, magna nulla aliquet sapien, ac fringilla odio tortor in eros. Duis a urna sem. Nunc ac purus mattis, pharetra urna quis, ultrices quam. Proin ac sollicitudin dolor, ac feugiat turpis. Sed aliquet ornare nisi, vitae finibus tortor vehicula auctor.</p>

    <div class="closing">Regards</div>
    <div class="signature-area" role="img" aria-label="Handwritten signature of the sender"></div>
    <div class="sender-name">Your Name Here</div>
    <div class="sender-role">Designation Here</div>

    <svg class="contact-icon phone-icon" width="32" height="32" viewBox="0 0 32 32" aria-hidden="true">
      <circle cx="16" cy="16" r="14" fill="none" stroke="var(--brand-green)" stroke-width="2.2"/>
      <path fill="var(--brand-green)" d="M11.5 8.5 l3 3.2 -1.6 2 q1.6 3.2 4.6 4.7 l2 -1.6 3.2 3 -1.6 2.4 q-1 .8 -2.6 .3 q-6.4 -2.6 -9 -9 q-.5 -1.6 .3 -2.6 Z"/>
    </svg>
    <div class="contact-text phone-text">+12345689<br>+12345689</div>

    <svg class="contact-icon web-icon" width="30" height="30" viewBox="0 0 30 30" aria-hidden="true">
      <g fill="none" stroke="var(--brand-green)" stroke-width="1.5">
        <circle cx="15" cy="15" r="13"/>
        <ellipse cx="15" cy="15" rx="6" ry="13"/>
        <line x1="15" y1="2" x2="15" y2="28"/>
        <line x1="2" y1="15" x2="28" y2="15"/>
        <path d="M4.5 8.5 H25.5 M4.5 21.5 H25.5"/>
      </g>
    </svg>
    <div class="contact-text web-text">www.yourwebsite.com</div>

    <svg class="contact-icon mail-icon" width="28" height="20" viewBox="0 0 28 20" aria-hidden="true">
      <g fill="none" stroke="var(--brand-green)" stroke-width="1.5">
        <rect x="1" y="1" width="26" height="18"/>
        <path d="M1 1 L14 11 L27 1 M1 19 L10.5 8.5 M27 19 L17.5 8.5"/>
      </g>
    </svg>
    <div class="contact-text mail-text">yourgmail@.com</div>
  </div>
</body>
</html>
```